Tech business card design

We need an amazing business card design for our new business 'Pexla' a marketing tech startup based in Sydney, Australia. We provide an online marketplace for businesses to search and buy advertising media, connect with service providers and learn more about marketing. We wish to communicate 'cool tech', reliability and professionalism and design based around our logo.

Target Market(s)

Business Owners

Contact Information for Business Card

Name
Position
Email Address
Website
Phone Number

Font styles to use
Other font styles liked:
• Avenir & Avenir Next

Colors

Designer to choose colors to be used in the design.

```html
<!DOCTYPE html>
<html lang="en">
<head>
<meta charset="utf-8">
<title>Pexla Business Card</title>
<link rel="stylesheet" href="https://fonts.googleapis.com/css2?family=Open+Sans:wght@400;700;800&display=swap">
<style>
  :root {
    --backdrop: #a0cfe2;
    --card-front: #ffffff;
    --card-back: #414042;
    --navy: #13123a;
    --ink: #231f20;
    --muted: #3a3a3c;
    --white: #ffffff;
  }
  * { margin: 0; padding: 0; box-sizing: border-box; }
  html, body {
    width: 1200px; height: 1184px; overflow: hidden;
    background: var(--backdrop);
    font-family: "Open Sans", sans-serif;
  }
  .canvas { position: relative; width: 1200px; height: 1184px; }
  .card { position: absolute; width: 902px; height: 515px; }
  .card--front { left: 147px; top: 53px; background: var(--card-front); }
  .card--back { left: 149px; top: 609px; background: var(--card-back); }

  .wordmark {
    position: absolute; font-weight: 800; letter-spacing: -4px;
    line-height: 1; white-space: nowrap;
  }
  .wordmark .tm { font-size: 16px; letter-spacing: 0; margin-left: 8px; font-weight: 700; }
  .card--front .wordmark { color: var(--navy); font-size: 158px; left: 232px; top: 18px; }
  .card--back .wordmark { color: var(--white); font-size: 158px; left: 230px; top: 130px; }

  .rules { position: absolute; left: 0; top: 0; }

  .person { position: absolute; left: 165px; top: 342px; }
  .person__name { font-weight: 700; font-size: 27px; color: var(--navy); line-height: 1.3; }
  .person__role { font-size: 25px; color: var(--ink); line-height: 1.4; }

  .contact { position: absolute; left: 506px; top: 298px; color: var(--muted); font-size: 22px; }
  .contact__row { display: flex; align-items: center; height: 35px; }
  .contact__row svg { width: 21px; height: 21px; margin-right: 11px; flex: none; }
  .contact__web { letter-spacing: 2px; }
  .contact__address { margin-top: 12px; line-height: 31px; }

  .back-url {
    position: absolute; left: 0; width: 100%; top: 415px; text-align: center;
    color: var(--white); font-size: 29px; letter-spacing: 4px;
  }
</style>
</head>
<body>
<div class="canvas">
  <section class="card card--front">
    <div class="wordmark">pexla<span class="tm">TM</span></div>

    <svg class="rules" width="902" height="515" aria-hidden="true">
      <g stroke="var(--ink)" stroke-width="3">
        <line x1="314" y1="224" x2="582" y2="224"/>
        <line x1="290" y1="236" x2="611" y2="236"/>
        <line x1="314" y1="250" x2="582" y2="250"/>
      </g>
      <g stroke="var(--ink)" stroke-width="1.5">
        <line x1="445" y1="312" x2="445" y2="472"/>
        <line x1="450" y1="297" x2="450" y2="466"/>
        <line x1="454" y1="312" x2="454" y2="464"/>
      </g>
    </svg>

    <div class="person">
      <p class="person__name">JOHN SMITH</p>
      <p class="person__role">Position</p>
    </div>

    <div class="contact">
      <div class="contact__row">
        <svg viewBox="0 0 24 24" aria-hidden="true"><circle cx="12" cy="12" r="10.5" fill="none" stroke="var(--navy)" stroke-width="1.8"/><path d="M9 7l2 2-1 1.5c.6 1.6 1.8 2.8 3.5 3.5L15 13l2 2-1.5 2C11 16 8 13 7.5 8.5z" fill="var(--navy)"/></svg>
        <span>012-345-6789</span>
      </div>
      <div class="contact__row">
        <svg viewBox="0 0 24 24" aria-hidden="true"><rect x="1" y="5" width="22" height="14" fill="var(--navy)"/><path d="M1 5l11 8 11-8M1 19l8-7M23 19l-8-7" stroke="var(--white)" stroke-width="1.6" fill="none"/></svg>
        <span>info@pexla.com</span>
      </div>
      <div class="contact__row">
        <svg viewBox="0 0 24 24" aria-hidden="true"><g fill="none" stroke="var(--navy)" stroke-width="1.6"><circle cx="12" cy="12" r="10"/><ellipse cx="12" cy="12" rx="4.5" ry="10"/><line x1="2" y1="12" x2="22" y2="12"/><path d="M4 7h16M4 17h16"/></g></svg>
        <span class="contact__web">www.pexla.com</span>
      </div>
      <p class="contact__address">Street name City Name,<br>Zipcode,012345</p>
    </div>
  </section>

  <section class="card card--back">
    <div class="wordmark">pexla<span class="tm">TM</span></div>
    <p class="back-url">www.pexla.com</p>
  </section>
</div>
</body>
</html>
```